Harvest Gateway Fellowship Ministries needs a fresh new web design

We are an up and coming multicultural church that aims to bring people into a life changing encounter with God. We need a fresh and inviting website in order to increase our internet presence and make us easier to connect with.
Here are some of the basic requirements for the site:
• Clearly displayed address, service times, and contact info
• A staff profile page
• An area for a calendar with upcoming events and their details
• Social media buttons
• Group pages for the different ministries (youth, children’s church, men, etc…)
• An area for donations and eCommerce
• A resources page for assorted media (podcasts, sermons, videos, etc.…)
• An area for prayer requests.

```html
<!DOCTYPE html>
<html lang="en">
<head>
<meta charset="utf-8">
<title>Harvest Gateway Fellowship Ministries</title>
<link rel="stylesheet" href="https://fonts.googleapis.com/css2?family=Lato:wght@400;700&family=Dosis:wght@500;600&family=Dancing+Script:wght@600&display=swap">
<style>
:root{
  --orange:#e5582a;
  --orange-dark:#c9461d;
  --green:#4fa93f;
  --green-dark:#3c8a2f;
  --page:#f1f0ed;
  --ink:#333;
  --muted:#666;
  --rule:#dcdad5;
  --white:#fff;
}
*{margin:0;padding:0;box-sizing:border-box}
html,body{width:694px;height:1200px;overflow:hidden}
body{position:relative;background:var(--page);font-family:Lato,Arial,sans-serif;color:var(--ink);font-size:7px;line-height:1.45}
.abs{position:absolute}
a{color:inherit;text-decoration:none}

.topbar{left:0;top:0;width:694px;height:22px;background:var(--orange);color:var(--white);font-size:7px}
.topbar .tagline{left:58px;top:6px}
.topbar .sched-label{left:426px;top:6px;font-size:7.5px}
.topbar .sched{left:533px;top:3px;font-size:6.5px;line-height:1.3;border-left:1px solid rgba(255,255,255,.7);padding-left:6px}

.header{left:0;top:22px;width:694px;height:84px;background:var(--white)}
.brand{left:58px;top:14px;display:flex;align-items:center;gap:5px;width:150px}
.brand .mark{width:14px;height:14px;border-radius:50%;background:var(--orange);flex:none}
.brand .name{font-weight:700;font-size:10px;line-height:1.15;color:var(--orange)}
.info{text-align:right;font-size:7px;color:var(--muted);line-height:1.35}
.info h3{color:var(--orange);font-size:9px;font-weight:700;margin-bottom:2px}
.info .more{color:var(--green);font-size:6.5px}
.info-donate{left:232px;top:16px;width:100px}
.info-prayer{left:352px;top:16px;width:142px;border-left:1px solid var(--rule);padding-top:0}
.info-address{left:507px;top:16px;width:90px;border-left:1px solid var(--rule)}
.divider-v{width:1px;height:40px;background:var(--rule)}
.social{left:621px;width:15px;height:15px;border-radius:50%;background:#b9b9b9}

.nav{left:66px;top:90px;width:564px;height:30px}
.nav ul{list-style:none;position:absolute;left:14px;top:0;width:536px;height:28px;display:flex;justify-content:space-between;align-items:center;padding:0 16px;color:var(--white);font-size:7.8px}

.hero{left:0;top:106px;width:694px;height:206px;background:linear-gradient(180deg,#e9e4da 0%,#d9cdb4 45%,#b98e3c 70%,#8d6620 100%)}
.hero .kicker{left:98px;top:60px;font-family:'Dancing Script',cursive;color:var(--orange);font-size:17px}
.hero .headline{left:97px;top:80px;font-family:Dosis,sans-serif;font-weight:600;color:var(--orange);font-size:20px;letter-spacing:.3px}
.hero .tail{left:296px;top:98px;font-family:'Dancing Script',cursive;color:var(--orange);font-size:15px}
.arrow{width:12px;height:24px;background:rgba(255,255,255,.85);top:194px}

.pastor-band{left:0;top:312px;width:694px;height:56px;background:var(--orange)}
.avatar{left:60px;top:295px;width:84px;height:84px;border-radius:50%;background:radial-gradient(circle at 50% 40%,#a7764f,#5a3a24);border:4px solid var(--orange-dark)}
.quote{left:150px;top:326px;color:var(--white);font-size:7.2px;line-height:1.3;border-left:1px solid rgba(255,255,255,.7);padding-left:11px}

.features{left:57px;top:389px;width:580px;height:156px;background:var(--page);border-top:2px solid #e2e0dc;border-radius:4px}
.card{top:397px;width:137px;text-align:center}
.card .photo{height:80px;position:relative}
.card .label{position:absolute;left:0;bottom:0;width:100%;height:22px;background:rgba(220,85,38,.92);color:var(--white);font-size:8.8px;line-height:22px}
.card p{font-size:7px;color:var(--muted);margin-top:6px;line-height:1.5;padding:0 2px}
.btn{display:inline-block;width:64px;height:17px;line-height:17px;background:var(--green);color:var(--white);font-size:7px;border-radius:2px;margin-top:7px}
.rule{left:57px;top:548px;width:580px;height:1px;background:#e2e0dc}

.section-title{font-size:12.5px;color:var(--orange);letter-spacing:.2px;border-bottom:1px solid var(--orange);padding-bottom:4px}
.news{left:63px;top:566px;width:365px}
.news-item{left:63px;width:365px;height:72px}
.news-item .thumb{position:absolute;left:0;top:0;width:116px;height:72px;border-radius:3px}
.news-item .body{position:absolute;left:127px;top:0;width:238px}
.news-item h4{font-size:10.3px;line-height:1.2;color:#3a3a3a;margin-bottom:3px}
.news-item p{font-size:6.6px;color:var(--muted);line-height:1.55}
.news-item .read{font-size:7px;color:var(--green);margin-top:3px}

.events{left:457px;top:566px;width:180px}
.event{left:457px;width:180px;border-bottom:1px solid var(--rule);height:67px}
.event .date{font-size:15px;color:var(--orange);line-height:1}
.event .date b{font-weight:700}
.event .date span{font-weight:400;margin-left:2px}
.event h4{font-size:10px;color:#3a3a3a;font-weight:400;margin-top:3px}
.event p{font-size:6.6px;color:var(--muted);margin-top:2px;line-height:1.5}
.event.active h4,.event.active p{color:var(--green)}

.map{left:0;top:884px;width:694px;height:144px;background:linear-gradient(135deg,#e8e6df,#dfe4d6 50%,#e9e6de)}
.pin{left:350px;top:935px}

.footer{left:0;top:1028px;width:694px;height:172px;background:var(--orange);color:#fbe2d6}
.footer h5{font-size:10.5px;font-weight:400;color:#fde4d8;margin-bottom:6px;letter-spacing:.2px}
.footer .col{top:1049px;font-size:7px;line-height:1.5}
.footer ul{list-style:none;columns:2;column-gap:6px;width:130px}
.footer li::before{content:"• "}
.footer .contact-line{display:flex;align-items:center;gap:6px;margin-top:4px}
.field{width:131px;height:18px;background:var(--white);border-radius:2px;color:#bbb;padding-left:7px;line-height:18px;margin-top:4px}
.subscribe{display:inline-block;background:var(--green);color:var(--white);padding:0 9px;height:18px;line-height:18px;border-radius:2px;margin-top:8px}
.footer-social{width:18px;height:18px;border-radius:50%;background:#f4a17d;display:inline-block;margin-right:4px;margin-top:5px}
.footer .rule-f{left:58px;top:1154px;width:578px;height:1px;background:rgba(255,255,255,.25)}
.copyright{left:0;top:1165px;width:694px;text-align:center;font-size:6.5px;color:#fbd5c4}
</style>
</head>
<body>

<div class="abs topbar">
  <div class="abs tagline">A house of prayer for all nations, where the love, the presence and the power of God are real.</div>
  <div class="abs sched-label">SUNDAY SERVICE SCHEDULE</div>
  <div class="abs sched">09:00 A.M. | Sunday School<br>10:30 A.M. | Convergent Service</div>
</div>

<header class="abs header">
  <div class="abs brand"><span class="mark"></span><span class="name">Harvest Gateway Fellowship Ministries</span></div>
  <div class="abs info info-donate">
    <h3>Donate</h3>
    Lorem Ipsum is simply<br>dummy text of the printing<br><a class="more" href="#">Donate Now »</a>
  </div>
  <div class="abs info info-prayer">
    <h3>Request Prayer</h3>
    Lorem Ipsum is simply dummy text<br>of the printing and typesetting industry.<br><a class="more" href="#">Request Now »</a>
  </div>
  <div class="abs info info-address">
    <h3>Address</h3>
    Harvest Gateway<br>City, Location<br><a class="more" href="#">Contact »</a>
  </div>
  <span class="abs social" style="top:18px"></span>
  <span class="abs social" style="top:36px"></span>
</header>

<svg class="abs nav" viewBox="0 0 564 30" width="564" height="30" aria-hidden="true">
  <polygon points="0,2 14,2 14,28 0,28 6,15" fill="#3c8a2f"/>
  <polygon points="564,2 550,2 550,28 564,28 558,15" fill="#3c8a2f"/>
  <polygon points="14,28 20,30 20,28" fill="#2a6421"/>
  <polygon points="550,28 544,30 544,28" fill="#2a6421"/>
  <rect x="14" y="0" width="536" height="28" fill="#4fa93f"/>
</svg>
<nav class="abs nav">
  <ul>
    <li>Home</li><li>About</li><li>Staff Profile</li><li>Worship &amp; Services</li><li>News &amp; Events</li><li>Groups</li><li>Shop</li><li>Resources</li><li>Contact</li>
  </ul>
</nav>

<section class="abs hero" role="img" aria-label="Photo of a man with raised arms in a golden wheat field under a pale sky">
  <div class="abs kicker">Feel the</div>
  <div class="abs headline">LOVE, PRESENCE &amp; POWER</div>
  <div class="abs tail">of God</div>
</section>
<span class="abs arrow" style="left:0;border-radius:0 12px 12px 0"></span>
<span class="abs arrow" style="left:682px;border-radius:12px 0 0 12px"></span>

<div class="abs pastor-band"></div>
<div class="abs avatar" role="img" aria-label="Portrait photo of the senior pastor"></div>
<div class="abs quote">Rev. Daniel Osei<br>La parole de Jésus et un Coeur qui est prêt forment une combinaison qui ne manque jamais de produire des miracles...</div>

<div class="abs features"></div>
<div class="abs card" style="left:64px">
  <div class="photo" role="img" aria-label="Photo of a studio microphone beside a globe" style="background:linear-gradient(135deg,#2b2b2b,#5a6f86 60%,#c98a2e)"><span class="label">RADIO SHOWS</span></div>
  <p>Lorem Ipsum is simply dummy text of the printing and typesetting industry..</p>
  <a class="btn" href="#">Know More</a>
</div>
<div class="abs card" style="left:207px">
  <div class="photo" role="img" aria-label="Photo of a bright church interior with pews" style="background:linear-gradient(180deg,#f2efe9,#c9c1b6 60%,#8c6d55)"><span class="label">SUNDAY SERVICE</span></div>
  <p>Lorem Ipsum is simply dummy text of the printing and typesetting industry..</p>
  <a class="btn" href="#">Know More</a>
</div>
<div class="abs card" style="left:350px">
  <div class="photo" role="img" aria-label="Photo of hands holding a donate sign" style="background:linear-gradient(135deg,#4a4036,#bfae97 55%,#6b5a49)"><span class="label">DONATE FOR A CAUSE</span></div>
  <p>Lorem Ipsum is simply dummy text of the printing and typesetting industry..</p>
  <a class="btn" href="#">Know More</a>
</div>
<div class="abs card" style="left:494px">
  <div class="photo" role="img" aria-label="Photo of folded hands in prayer" style="background:linear-gradient(135deg,#2e1f18,#8a5a42 55%,#3a2720)"><span class="label">PRAYER REQUEST</span></div>
  <p>Lorem Ipsum is simply dummy text of the printing and typesetting industry..</p>
  <a class="btn" href="#">Know More</a>
</div>
<div class="abs rule"></div>

<h2 class="abs news section-title" style="font-weight:400">LATEST NEWS</h2>
<article class="abs news-item" style="top:604px">
  <div class="thumb" role="img" aria-label="Photo of a small group studying together" style="background:linear-gradient(135deg,#d9dde2,#8c97a6 50%,#c2a68a)"></div>
  <div class="body">
    <h4>Lorem Ipsum is simply dummy text of the printing and typesetting industry.</h4>
    <p>Lorem Ipsum is simply dummy text of the printing and typesetting industry. Lorem Ipsum has been the industry's standard dummy text ever since the 1500s..</p>
    <div class="read">Read More</div>
  </div>
</article>
<article class="abs news-item" style="top:693px">
  <div class="thumb" role="img" aria-label="Photo of a crowd gathered outdoors under trees" style="background:linear-gradient(180deg,#6e8f4a,#3d5a2c 55%,#8a7a6a)"></div>
  <div class="body">
    <h4>Lorem Ipsum is simply dummy text.</h4>
    <p>Lorem Ipsum is simply dummy text of the printing and typesetting industry. Lorem Ipsum has been the industry's standard dummy text ever since the 1500s, when an unknown printer took a galley of type and scrambled it to make a type specimen book..</p>
    <div class="read">Read More</div>
  </div>
</article>
<article class="abs news-item" style="top:782px">
  <div class="thumb" role="img" aria-label="Photo of lit candles in the dark" style="background:radial-gradient(circle at 50% 55%,#f2a23a,#a4460f 45%,#2a1206)"></div>
  <div class="body">
    <h4>Lorem Ipsum is simply dummy text printing.</h4>
    <p>Lorem Ipsum is simply dummy text of the printing and typesetting industry. Lorem Ipsum has been the industry's standard dummy text ever since the 1500s, when an unknown printer took a galley of type and scrambled it to make a type specimen book..</p>
    <div class="read">Read More</div>
  </div>
</article>

<h2 class="abs events section-title" style="font-weight:400">UPCOMING EVENTS</h2>
<div class="abs event" style="top:603px">
  <div class="date"><b>26</b><span>JUN</span></div>
  <h4>Vacation Bible School</h4>
  <p>Lorem Ipsum is simply dummy text of the printing and typesetting industry.</p>
</div>
<div class="abs event active" style="top:671px">
  <div class="date"><b>27</b><span>JUN</span></div>
  <h4>Vacation Bible School</h4>
  <p>Lorem Ipsum is simply dummy text of the printing and typesetting industry.</p>
</div>
<div class="abs event" style="top:739px">
  <div class="date"><b>28</b><span>JUN</span></div>
  <h4>Vacation Bible School</h4>
  <p>Lorem Ipsum is simply dummy text of the printing and typesetting industry.</p>
</div>
<div class="abs event" style="top:807px;border-bottom:none">
  <div class="date"><b>29</b><span>JUN</span></div>
  <h4>Family and Friends Day</h4>
  <p>Sunday June 29th is our family and friends day with special guest pastor Samuel Reyes. Come with faith..</p>
</div>

<div class="abs map" role="img" aria-label="Road map showing the church location"></div>
<svg class="abs pin" width="30" height="38" viewBox="0 0 30 38" aria-hidden="true">
  <path d="M15 1C7 1 1 7 1 15c0 10 14 22 14 22s14-12 14-22C29 7 23 1 15 1z" fill="#4fa93f"/>
  <circle cx="15" cy="15" r="8" fill="#fff"/>
  <circle cx="15" cy="15" r="4" fill="#e5582a"/>
</svg>

<footer class="abs footer"></footer>
<div class="abs col footer" style="left:58px;width:120px;height:auto;background:none">
  <h5>CONTACT US</h5>
  Harvest Gateway<br>Location, city<br>State Name, Country
  <div class="contact-line" style="margin-top:8px">
    <svg width="8" height="8" viewBox="0 0 10 10" aria-hidden="true"><path d="M2 1l2 0 1 3-1.5 1a6 6 0 0 0 2.5 2.5L7 6l3 1v2c0 .5-.5 1-1 1A9 9 0 0 1 0 2c0-.5.5-1 1-1z" fill="#fde4d8"/></svg>
    +1 555-014-2290
  </div>
  <div class="contact-line">
    <svg width="9" height="7" viewBox="0 0 10 8" aria-hidden="true"><rect x=".5" y=".5" width="9" height="7" fill="none" stroke="#fde4d8"/><path d="M.5 .5L5 4.5 9.5 .5" fill="none" stroke="#fde4d8"/></svg>
    hello@harvestgateway.org
  </div>
</div>
<div class="abs col footer" style="left:186px;width:150px;height:auto;background:none">
  <h5>COMMUNITIES WE SERVE</h5>
  <ul>
    <li>Lorem Ipsum</li><li>Dummy Links</li><li>More dummy</li><li>Sample Text</li><li>More samples</li>
    <li>type text dummy</li><li>Lorem Ipsum</li>
  </ul>
</div>
<div class="abs col footer" style="left:346px;width:140px;height:auto;background:none">
  <h5>NEWSLETTER</h5>
  Enter your email below to get notified
  <div class="field">Your Email</div>
  <span class="subscribe">Subscribe</span>
</div>
<div class="abs col footer" style="left:507px;width:135px;height:auto;background:none">
  <h5>CONNECT WITH US</h5>
  Stay connected for the latest updates at Riverside Community Church<br>
  <span class="footer-social"></span><span class="footer-social"></span>
</div>
<div class="abs rule-f footer" style="height:1px;background:rgba(255,255,255,.25)"></div>
<div class="abs copyright">Copyright © 2014. All rights reserved. Harvest Gateway.</div>

</body>
</html>
```